Online interactive tutorial for year 2 to year 12 students in Australia

Website design for a new online tutorial for year 2 to year 12 students in Australia.

- The tutorial will be conducted via live webcam and within a dedicated interactive space
- The tutorial will be provided by high scoring undergraduates studying in top Australian universities.
- The tutors will be going through interviews & assessments & only top students are allowed to apply.
- Parents will do search and select tutor and have short 15 mins video interaction with potential tutors before booking them for their children for tutoring.
- hourly cost of booking (no monthly subscription or no hour limits)
- Tutors will have their own profile

Please see the attached for detailed page functionality.

The look and feel of the design must consider the following:
- must be educational but not dull and should stand out
- must appeal to younger generation - tutees (8-18 years), tutors (19-25), parents (30-50).
- Ideas for Logos (brivora.com.au but not confirmed)

Target Market(s)

tutees (8-18 years), tutors (19-25 years), parents (30-50 years).

Industry/Entity Type

Education

Coding

Coded - Design and coding required

Number of Pages Required

5+ page

Font styles to use
Serif

Requirements
Must have
• The look and feel of the design must consider the following:
• - must be educational but not dull and should stand out
• - must appeal to younger generation - tutees (8-18 years), tutors (19-25), parents (30-50).
Should not have
• Dullness

```html
<!DOCTYPE html>
<html lang="en">
<head>
<meta charset="utf-8">
<title>Brivora – Online Tutoring</title>
<link rel="stylesheet" href="https://fonts.googleapis.com/css2?family=Lora:ital,wght@0,400;0,700;1,400&family=Open+Sans:ital,wght@0,400;0,600;1,400&display=swap">
<style>
:root{
  --green:#2ea84f;
  --green-bright:#37c15d;
  --navy:#232a45;
  --navy-dark:#1b2138;
  --ink:#333;
  --muted:#8a8a8a;
  --card-grey:#f2f2f2;
  --footer:#2b2b2b;
  --footer-base:#212121;
  --white:#fff;
}
*{box-sizing:border-box;margin:0;padding:0}
html,body{width:1200px;height:2211px;overflow:hidden}
body{position:relative;background:var(--white);font-family:"Open Sans",Arial,sans-serif;color:var(--ink)}
.abs{position:absolute}

/* header */
.brand{left:133px;top:20px;font-family:"Lora",Georgia,serif;font-weight:700;font-size:40px;color:var(--green);line-height:48px}
.btn{top:22px;height:37px;color:#fff;font-size:13px;display:flex;align-items:center;justify-content:center;border-radius:2px}
.btn-register{left:688px;width:80px;background:var(--green)}
.btn-login{left:777px;width:78px;background:var(--navy)}
.search{left:865px;top:22px;width:201px;height:37px;border:1px solid #ddd;font-size:11px;color:#aaa;padding:0 16px;display:flex;align-items:center;justify-content:space-between}

/* nav */
.nav{left:0;top:84px;width:1200px;height:40px;background:var(--green);display:flex;padding-left:133px}
.nav a{color:#fff;font-family:"Lora",Georgia,serif;font-size:12.2px;text-decoration:none;padding:0 11px;line-height:40px}
.nav a.active{background:var(--navy)}

/* hero */
.hero{left:0;top:124px;width:1200px;height:489px;background:linear-gradient(100deg,#6b5a48 0%,#a98d6d 30%,#c79b7d 50%,#8b7b63 72%,#d9cdb7 100%)}
.hero-title{left:0;top:394px;width:1200px;text-align:center;color:#fff;font-family:"Lora",Georgia,serif;font-weight:700;font-size:27px;text-shadow:0 1px 3px rgba(0,0,0,.4)}
.hero-arrow{top:352px;width:16px;height:30px;background:rgba(0,0,0,.25)}

/* features */
.feature{width:295px;height:200px;background:var(--navy);color:#fff;text-align:center;padding-top:30px}
.feature svg{height:34px}
.feature h3{font-family:"Lora",Georgia,serif;font-weight:400;font-size:21px;margin-top:10px}
.feature p{font-size:10px;line-height:17.5px;color:#b8bccb;margin:10px 18px 0}

/* testimonials / get started */
.testi-bg{left:0;top:1101px;width:600px;height:345px;background:linear-gradient(120deg,#2fae50,#41c463 60%,#2fa94d)}
.start-bg{left:600px;top:1101px;width:600px;height:345px;background:linear-gradient(110deg,#3a4257,#2c3347 60%,#4b5263)}
.section-title{font-family:"Lora",Georgia,serif;font-weight:700;font-size:36px}
.avatar{left:133px;top:1208px;width:182px;height:182px;border-radius:50%;background:radial-gradient(circle at 50% 40%,#e9c8a9,#6b86a3 75%);border:3px solid #fff}
.quote-name{left:330px;top:1198px;color:#fff;font-size:22px}
.quote-role{left:330px;top:1228px;color:#eaffef;font-size:12.5px}
.quote{left:330px;top:1255px;width:230px;color:#fff;font-style:italic;font-size:12.5px;line-height:19px}
.dots{left:331px;top:1405px;display:flex;gap:11px}
.dots span{width:12px;height:12px;border-radius:50%;background:#fff}
.dots span.on{background:transparent;border:2px solid #fff}
.field{background:#fff;font-size:10.5px;color:#888;padding:0 16px;display:flex;align-items:center}
.cta{left:662px;top:1381px;width:171px;height:41px;background:var(--green-bright);color:#fff;font-family:"Lora",Georgia,serif;font-size:14px;display:flex;align-items:center;justify-content:center}

/* tutors */
.pager{top:1497px;width:25px;height:22px;border:1px solid #aaa;display:flex;align-items:center;justify-content:center}
.tutor{width:287px;height:104px;background:var(--card-grey)}
.tutor .photo{position:absolute;left:0;top:0;width:99px;height:104px;background:linear-gradient(160deg,#d8d2cb,#8f8178)}
.tutor .info{position:absolute;left:112px;top:18px;font-size:9.5px;line-height:15px;color:#333}
.tutor .handle{color:#aaa;font-size:8.5px;margin-top:6px}
.tutor .social{display:flex;gap:10px;margin-top:8px}
.tutor .social span{width:7px;height:7px;border-radius:50%;background:#aaa}

/* stats */
.stats{left:0;top:1842px;width:1200px;height:136px;background:linear-gradient(90deg,#dcdcdc,#ececec 50%,#d6d6d6)}
.stat{width:300px;text-align:center}
.stat b{display:block;font-family:"Lora",Georgia,serif;font-weight:400;font-size:41px;color:#1f2437;line-height:48px}
.stat span{font-family:"Lora",Georgia,serif;font-size:13px;color:#444}

/* footer */
.footer{left:0;top:1978px;width:1200px;height:177px;background:var(--footer)}
.footer-base{left:0;top:2155px;width:1200px;height:56px;background:var(--footer-base)}
.foot-head{font-size:12px;color:var(--green-bright);top:2009px}
.foot-list{top:2034px;list-style:none;font-size:10px;color:#bbb;line-height:19px}
.foot-list li:before{content:"• ";color:#888}
.divider{top:2010px;width:1px;height:120px;background:#444}
.newsletter{left:846px;top:2039px;width:220px;height:35px;background:#fff;font-size:10px;color:#666;padding-left:14px;display:flex;align-items:center}
.newsletter i{position:absolute;right:0;top:0;width:27px;height:35px;background:var(--green-bright)}
.copyright{left:133px;top:2173px;font-size:10px;color:#bbb}
.social-dot{top:2168px;width:27px;height:27px;border-radius:50%;border:1.5px solid #ddd}
</style>
</head>
<body>

<!-- header -->
<div class="abs brand">Brivora</div>
<div class="abs btn btn-register">Register</div>
<div class="abs btn btn-login">Login</div>
<div class="abs search">Search
  <svg width="14" height="14" viewBox="0 0 14 14"><circle cx="6" cy="6" r="4.3" fill="none" stroke="#2ea84f" stroke-width="2"/><line x1="9.2" y1="9.2" x2="13" y2="13" stroke="#2ea84f" stroke-width="2.2"/></svg>
</div>

<nav class="abs nav">
  <a class="active">Home</a><a>Tutor Registration</a><a>Parent Registration</a><a>Student Log-ins</a><a>Note Space</a><a>Tutor Profile</a><a>Scheduler</a><a>Payment</a><a>Tutor Feedback</a><a>More</a>
</nav>

<!-- hero -->
<div class="abs hero" role="img" aria-label="Photo of a young student studying at a laptop in a library, with a stack of books"></div>
<div class="abs hero-arrow" style="left:0"></div>
<div class="abs hero-arrow" style="left:1184px"></div>
<svg class="abs" style="left:567px;top:318px" width="66" height="66" viewBox="0 0 66 66">
  <circle cx="33" cy="33" r="30" fill="none" stroke="#fff" stroke-width="4"/>
  <polygon points="26,20 47,33 26,46" fill="#fff"/>
</svg>
<div class="abs hero-title">How It Works</div>

<!-- features -->
<div class="abs feature" style="left:133px;top:643px">
  <svg viewBox="0 0 40 30" width="46"><polygon points="20,3 39,11 20,19 1,11" fill="#fff"/><path d="M9 15v7c0 3 22 3 22 0v-7l-11 5z" fill="#fff"/><rect x="35" y="11" width="2" height="11" fill="#fff"/></svg>
  <h3>Learn With us</h3>
  <p>Donec nec velit quis turpis molestie lobortis eu a nisi. In vulputate felis nec diam tempor, sit amet dapibus enim hendrerit. In tristique rutrum tellus.</p>
</div>
<div class="abs feature" style="left:452px;top:643px">
  <svg viewBox="0 0 44 34" width="46"><circle cx="22" cy="8" r="6" fill="#fff"/><circle cx="9" cy="12" r="4.5" fill="#fff"/><circle cx="35" cy="12" r="4.5" fill="#fff"/><path d="M12 32c0-10 20-10 20 0z" fill="#fff"/><path d="M1 30c0-8 13-9 13-3v3z M43 30c0-8-13-9-13-3v3z" fill="#fff"/></svg>
  <h3>High Scoring Undergrad</h3>
  <p>Donec nec velit quis turpis molestie lobortis eu a nisi. In vulputate felis nec diam tempor, sit amet dapibus enim hendrerit. In tristique rutrum tellus.</p>
</div>
<div class="abs feature" style="left:771px;top:643px">
  <svg viewBox="0 0 40 30" width="42"><rect x="1" y="1" width="38" height="28" rx="4" fill="#fff"/><polygon points="15,8 28,15 15,22" fill="#232a45"/></svg>
  <h3>Search and Select Tutor</h3>
  <p>Donec nec velit quis turpis molestie lobortis eu a nisi. In vulputate felis nec diam tempor, sit amet dapibus enim hendrerit. In tristique rutrum tellus.</p>
</div>
<div class="abs feature" style="left:133px;top:870px">
  <svg viewBox="0 0 30 36" width="32"><ellipse cx="15" cy="6" rx="13" ry="5" fill="#fff"/><path d="M2 10c0 6 26 6 26 0v6c0 6-26 6-26 0z M2 20c0 6 26 6 26 0v6c0 6-26 6-26 0z" fill="#fff"/></svg>
  <h3>Dedicated Interactive Space</h3>
  <p>Donec nec velit quis turpis molestie lobortis eu a nisi. In vulputate felis nec diam tempor, sit amet dapibus enim hendrerit. In tristique rutrum tellus.</p>
</div>
<div class="abs feature" style="left:452px;top:870px">
  <svg viewBox="0 0 42 28" width="42"><rect x="1" y="2" width="28" height="24" rx="4" fill="#fff"/><polygon points="30,14 41,5 41,23" fill="#fff"/></svg>
  <h3>Live Webcam</h3>
  <p>Donec nec velit quis turpis molestie lobortis eu a nisi. In vulputate felis nec diam tempor, sit amet dapibus enim hendrerit. In tristique rutrum tellus.</p>
</div>
<div class="abs feature" style="left:771px;top:870px">
  <svg viewBox="0 0 42 28" width="42"><rect x="1" y="2" width="40" height="24" fill="#fff"/><rect x="5" y="6" width="32" height="16" fill="#232a45"/><circle cx="21" cy="14" r="6" fill="#fff"/><rect x="20" y="10" width="2" height="8" fill="#232a45"/></svg>
  <h3>Hourly Cost of Booking</h3>
  <p>Donec nec velit quis turpis molestie lobortis eu a nisi. In vulputate felis nec diam tempor, sit amet dapibus enim hendrerit. In tristique rutrum tellus.</p>
</div>

<!-- testimonials -->
<div class="abs testi-bg"></div>
<div class="abs start-bg" role="img" aria-label="Dimmed photo of a student working on a laptop"></div>
<div class="abs section-title" style="left:133px;top:1124px;color:#fff">Testimonials</div>
<div class="abs avatar" role="img" aria-label="Portrait photo of a smiling young student"></div>
<div class="abs quote-name">Evan Marsh</div>
<div class="abs quote-role">Cras lacinia malesuada</div>
<p class="abs quote">“ Donec nec velit quis turpis molestie lobortis eu a nisi. In vulputate felis nec diam tempor, sit amet dapibus enim hendrerit. In tristique rutrum tellus, non tincidunt enim porttitor at. Fusce facilisis faucibus massa. Sed vitae malesuada dui, ut aliquet diam ”</p>
<div class="abs dots"><span class="on"></span><span></span><span></span><span></span></div>

<!-- get started -->
<div class="abs section-title" style="left:659px;top:1124px;color:var(--green-bright)">Get Started Now</div>
<div class="abs field" style="left:662px;top:1190px;width:196px;height:33px">Name</div>
<div class="abs field" style="left:870px;top:1190px;width:196px;height:33px">Email</div>
<div class="abs field" style="left:662px;top:1238px;width:196px;height:34px">Phone</div>
<div class="abs field" style="left:870px;top:1238px;width:196px;height:34px;justify-content:space-between">For Tutees
  <svg width="9" height="6" viewBox="0 0 9 6"><polygon points="0,0 9,0 4.5,6" fill="#555"/></svg>
</div>
<div class="abs field" style="left:662px;top:1285px;width:404px;height:84px;align-items:flex-start;padding-top:12px">Message</div>
<div class="abs cta">GET STARTED NOW</div>

<!-- tutors -->
<div class="abs pager" style="left:439px"><svg width="7" height="10" viewBox="0 0 7 10"><polyline points="6,1 2,5 6,9" fill="none" stroke="#888" stroke-width="1.5"/></svg></div>
<div class="abs section-title" style="left:0;top:1484px;width:1200px;text-align:center;color:var(--green-bright)">Our Tutors</div>
<div class="abs pager" style="left:733px"><svg width="7" height="10" viewBox="0 0 7 10"><polyline points="1,1 5,5 1,9" fill="none" stroke="#888" stroke-width="1.5"/></svg></div>

<div class="abs tutor" style="left:133px;top:1555px"><div class="photo" role="img" aria-label="Portrait photo of an older male tutor"></div><div class="info">Evan Marsh,<br>Nam et nisi id felis ullamcorper.<div class="handle">Chat : evan_marsh27</div><div class="social"><span></span><span></span><span></span></div></div></div>
<div class="abs tutor" style="left:455px;top:1555px"><div class="photo" role="img" aria-label="Portrait photo of a female tutor"></div><div class="info">Evan Marsh,<br>Nam et nisi id felis ullamcorper.<div class="handle">Chat : evan_marsh27</div><div class="social"><span></span><span></span><span></span></div></div></div>
<div class="abs tutor" style="left:778px;top:1555px"><div class="photo" role="img" aria-label="Portrait photo of a male tutor in a suit"></div><div class="info">Evan Marsh,<br>Nam et nisi id felis ullamcorper.<div class="handle">Chat : evan_marsh27</div><div class="social"><span></span><span></span><span></span></div></div></div>
<div class="abs tutor" style="left:133px;top:1692px"><div class="photo" role="img" aria-label="Portrait photo of a female tutor"></div><div class="info">Evan Marsh,<br>Nam et nisi id felis ullamcorper.<div class="handle">Chat : evan_marsh27</div><div class="social"><span></span><span></span><span></span></div></div></div>
<div class="abs tutor" style="left:455px;top:1692px"><div class="photo" role="img" aria-label="Portrait photo of a male tutor"></div><div class="info">Evan Marsh,<br>Nam et nisi id felis ullamcorper.<div class="handle">Chat : evan_marsh27</div><div class="social"><span></span><span></span><span></span></div></div></div>
<div class="abs tutor" style="left:778px;top:1692px"><div class="photo" role="img" aria-label="Portrait photo of a female tutor"></div><div class="info">Evan Marsh,<br>Nam et nisi id felis ullamcorper.<div class="handle">Chat : evan_marsh27</div><div class="social"><span></span><span></span><span></span></div></div></div>

<!-- stats -->
<div class="abs stats" role="img" aria-label="Faded photo of students reading books"></div>
<div class="abs stat" style="left:123px;top:1872px"><b>23,154</b><span>Donec ac tincidunt augue</span></div>
<div class="abs stat" style="left:450px;top:1872px"><b>85%</b><span>Donec ac tincidunt augue</span></div>
<div class="abs stat" style="left:776px;top:1872px"><b>52,841</b><span>Donec ac tincidunt augue</span></div>

<!-- footer -->
<div class="abs footer"></div>
<div class="abs foot-head" style="left:133px">Links</div>
<ul class="abs foot-list" style="left:133px"><li>Home</li><li>Tutor Registration</li><li>Parent Registration</li><li>Student Log-ins</li><li>Note Space</li></ul>
<ul class="abs foot-list" style="left:287px"><li>Tutor Profile</li><li>Scheduler</li><li>Payment</li><li>Tutor Feedback</li><li>Website Feedback</li></ul>
<ul class="abs foot-list" style="left:438px"><li>Module Contents</li><li>Administration</li><li>About Us</li><li>Contact Us</li><li>Message</li></ul>
<div class="abs divider" style="left:585px"></div>
<div class="abs foot-head" style="left:644px">Support</div>
<ul class="abs foot-list" style="left:644px"><li>Terms of Use</li><li>Privacy Policy</li><li>Sitemap</li></ul>
<div class="abs divider" style="left:793px"></div>
<div class="abs foot-head" style="left:846px">Newsletter Subscribe</div>
<div class="abs newsletter">Email Address<i></i></div>

<div class="abs footer-base"></div>
<div class="abs copyright">Copyright © 2016 Brivora. All rights reserved.</div>
<div class="abs social-dot" style="left:975px"></div>
<div class="abs social-dot" style="left:1007px"></div>
<div class="abs social-dot" style="left:1039px"></div>

</body>
</html>
```